Tour operator needs simple coded WordPress site (updated extra payment for coding and guaranteed)

[update 9/7/2015]
If you design a new logo and it gets accepted, even if we use another template with your logo you will get $50
[update 8/7/2015]
Update on questions about dual-language
For dual languages we are happy to set up a second site with the same designs in a second language.
For the design aspect just allow the user to switch between languages with an icon.
For the coding, a replica of the site on a second server will do (to save messing around with multiple language plugins) - we will populate it with Chinese text
[original post]
Simple coded WordPress site for tours
You can choose to design only or design and code ($340 design, $150 bonus for coding)
Open design brief - use your creativity
Will be in 2 languages (English and Chinese) but design needs only to be in one language
Winning design will be chosen only from home page, but the winner must make a second standard template page when chosen at no extra cost.
Must be responsive design
We only need homepage and standard template page design and coding, we will populate the pages
You can use design ideas from our pamphlet if you like - attached
Only a sample logo and colors on website and pamphlet - feel free to change as the current ones seem restrictive
Current website framework only to give an idea of the number of pages and basic menu structure (no need to use existing navigation style or any style at all for that matter, open brief)
http://brightwattlejourneys.com.au/
Target Market(s)
Chinese parents of kids 10-14 (the kids will take the tour)
Industry/Entity Type
Tour
Number of Pages Required
2 page
Look and feel
Each slider illustrates characteristics of the customer's brand and the style your logo design should communicate.

```html
<!DOCTYPE html>
<html lang="en">
<head>
<meta charset="utf-8">
<title>Bright Wattle Journeys</title>
<link href="https://fonts.googleapis.com/css2?family=Oswald:wght@400;500&family=Open+Sans:wght@400;600;700&display=swap" rel="stylesheet">
<style>
:root{
  --teal:#17a5b9;
  --teal-dark:#11899b;
  --green:#8dbf3f;
  --orange:#f39a21;
  --ink:#3b3f45;
  --muted:#7c8188;
  --light:#eef0f1;
  --line:#dde1e4;
  --night:#1c2a33;
  --white:#ffffff;
}
*{box-sizing:border-box;margin:0;padding:0}
html,body{width:779px;height:1200px;overflow:hidden}
body{font-family:"Open Sans",Arial,sans-serif;color:var(--ink);background:var(--white);font-size:9px;line-height:1.5}
.site{width:779px;height:1200px;position:relative}

/* header */
.site-header{height:52px;display:flex;align-items:center;justify-content:space-between;padding:0 26px 0 34px;background:var(--white)}
.brand{display:flex;align-items:center;gap:8px;font-family:"Open Sans",sans-serif;font-weight:700;font-size:22px;color:var(--teal);letter-spacing:1px}
.brand-dot{width:14px;height:14px;border-radius:50%;background:var(--orange)}
.main-nav{display:flex;align-items:center;gap:20px;font-size:9px;font-weight:600;letter-spacing:.5px}
.main-nav a{color:var(--ink);text-decoration:none}
.lang{display:flex;gap:6px}
.lang span{width:16px;height:11px;display:block}
.lang .zh{background:#d52b1e}
.lang .en{background:#24408e}

/* hero */
.hero{position:relative;height:343px;background:linear-gradient(180deg,#1d3f78 0%,#3d6aa6 35%,#e9a64f 68%,#2c3e56 82%,#13202f 100%)}
.hero-title{position:absolute;left:40px;top:150px;font-family:"Oswald",sans-serif;font-weight:400;font-size:34px;line-height:1.15;color:var(--white);letter-spacing:1px}
.hero-title .accent{color:var(--green)}
.hero-arrows{position:absolute;right:20px;bottom:22px;display:flex;gap:2px}
.hero-arrows span{width:16px;height:16px;background:rgba(0,0,0,.55);display:flex;align-items:center;justify-content:center}

/* welcome */
.welcome{padding:28px 40px 0;text-align:center}
.section-title{font-family:"Oswald",sans-serif;font-weight:500;font-size:15px;letter-spacing:.5px;color:var(--ink)}
.section-title .accent{color:var(--teal)}
.rule{width:60px;height:2px;background:var(--green);margin:6px auto 10px}
.welcome p{text-align:left;color:var(--muted)}

/* features */
.features{display:flex;gap:20px;padding:26px 40px 0}
.feature{width:196px}
.feature-photo{height:120px;border:1px solid var(--line)}
.photo-harbour{background:linear-gradient(160deg,#8cc7e8,#d9c7a0 60%,#b7845a)}
.photo-class{background:linear-gradient(160deg,#e7ecef,#9cc8d8 50%,#5e8aa6)}
.feature h3{font-family:"Oswald",sans-serif;font-weight:500;font-size:10px;color:var(--green);margin:8px 0 3px;letter-spacing:.4px}
.feature p{color:var(--muted);font-size:8px}
.includes{width:267px;border:1px solid var(--line)}
.includes h3{background:var(--teal);color:var(--white);font-family:"Oswald",sans-serif;font-weight:500;font-size:11px;padding:7px 12px;letter-spacing:.5px}
.includes ul{list-style:none;padding:10px 14px 12px}
.includes li{display:flex;align-items:center;gap:6px;font-size:8px;color:var(--ink);padding:2px 0}

/* itinerary */
.itinerary{position:absolute;left:0;top:845px;width:779px;height:205px;background:var(--light);display:flex;justify-content:space-between;padding:30px 40px 0}
.itinerary-text{width:380px}
.itinerary h2{font-family:"Oswald",sans-serif;font-weight:500;font-size:17px;color:var(--green);letter-spacing:.5px;margin-bottom:8px}
.itinerary p{color:var(--muted);font-size:8.5px}
.btn{display:inline-block;margin-top:12px;background:var(--orange);color:var(--white);font-size:8px;font-weight:600;padding:5px 12px;border-radius:2px}
.video{width:262px;height:152px;border:1px solid #b9bec2;background:var(--white);padding:3px;position:relative}
.video-frame{height:125px;background:radial-gradient(circle at 50% 55%,#b8b3a8,#6f6a60 60%,#3f3c37)}
.video-play{position:absolute;left:50%;top:52px;transform:translateX(-50%)}
.video-bar{height:18px;background:#1f2326;display:flex;align-items:center;gap:6px;padding:0 6px}
.video-track{flex:1;height:2px;background:#6a6f73}

/* footer */
.site-footer{position:absolute;left:0;top:1050px;width:779px;height:130px;background:var(--teal);display:flex;gap:30px;padding:18px 40px 0;color:var(--white)}
.footer-col{width:150px}
.footer-col h4{font-family:"Oswald",sans-serif;font-weight:500;font-size:10px;letter-spacing:.5px;margin-bottom:8px}
.footer-col p{font-size:7.5px;line-height:1.55}
.signup-field{margin-top:6px;height:14px;background:var(--white);color:var(--muted);font-size:7px;padding:1px 5px}
.signup-btn{display:inline-block;margin-top:5px;background:var(--night);font-size:7px;padding:2px 8px}
.social{list-style:none}
.social li{display:flex;align-items:center;gap:6px;font-size:7.5px;margin-bottom:6px}
.social li span{width:12px;height:12px;border-radius:50%;background:var(--teal-dark);border:1px solid rgba(255,255,255,.6)}
.bottom-bar{position:absolute;left:0;top:1180px;width:779px;height:20px;background:var(--night);color:#c7cdd1;font-size:7px;text-align:center;line-height:20px}
</style>
</head>
<body>
<div class="site">
  <header class="site-header">
    <div class="brand"><span class="brand-dot"></span>BWJ</div>
    <nav class="main-nav">
      <a href="#">HOME</a><a href="#">TOURS</a><a href="#">CONTACT</a><a href="#">ABOUT US</a>
      <svg width="10" height="10" viewBox="0 0 10 10" aria-label="Search"><circle cx="4" cy="4" r="3" fill="none" stroke="#3b3f45" stroke-width="1.4"/><line x1="6.3" y1="6.3" x2="9.3" y2="9.3" stroke="#3b3f45" stroke-width="1.4"/></svg>
      <div class="lang"><span class="zh" aria-label="Chinese"></span><span class="en" aria-label="English"></span></div>
    </nav>
  </header>

  <section class="hero" role="img" aria-label="Sydney harbour at dusk with the opera house lit up">
    <h1 class="hero-title">BRIGHT<br><span class="accent">WATTLE</span><br>JOURNEYS</h1>
    <div class="hero-arrows">
      <span><svg width="6" height="8" viewBox="0 0 6 8"><path d="M5 0L1 4l4 4" fill="none" stroke="#fff" stroke-width="1.4"/></svg></span>
      <span><svg width="6" height="8" viewBox="0 0 6 8"><path d="M1 0l4 4-4 4" fill="none" stroke="#fff" stroke-width="1.4"/></svg></span>
    </div>
  </section>

  <section class="welcome">
    <h2 class="section-title">WELCOME TO <span class="accent">BRIGHT WATTLE JOURNEYS</span></h2>
    <div class="rule"></div>
    <p>Bright Wattle Journeys runs guided study tours across Australia for students aged ten to fourteen. Each trip blends classroom visits, city walks, wildlife parks and homestay evenings, so young travellers build confidence, practise English and make friends while parents stay informed every step of the way through daily updates from our caring tour leaders.</p>
  </section>

  <section class="features">
    <article class="feature">
      <div class="feature-photo photo-harbour" role="img" aria-label="Student looking out over the harbour"></div>
      <h3>SAFE AND SECURE</h3>
      <p>Every group travels with trained leaders, checked host families and round-the-clock support from our Sydney office.</p>
    </article>
    <article class="feature">
      <div class="feature-photo photo-class" role="img" aria-label="Students working together in a classroom"></div>
      <h3>EDUCATIONAL AND CULTURAL</h3>
      <p>Students visit schools, museums and galleries, learning about Australian history, language and everyday life.</p>
    </article>
    <aside class="includes">
      <h3>INCLUDES</h3>
      <ul>
        <li><svg width="8" height="8" viewBox="0 0 8 8"><path d="M1 4l2 2 4-5" fill="none" stroke="#8dbf3f" stroke-width="1.5"/></svg>Return tickets</li>
        <li><svg width="8" height="8" viewBox="0 0 8 8"><path d="M1 4l2 2 4-5" fill="none" stroke="#8dbf3f" stroke-width="1.5"/></svg>Visa fees</li>
        <li><svg width="8" height="8" viewBox="0 0 8 8"><path d="M1 4l2 2 4-5" fill="none" stroke="#8dbf3f" stroke-width="1.5"/></svg>Travel accident insurance</li>
        <li><svg width="8" height="8" viewBox="0 0 8 8"><path d="M1 4l2 2 4-5" fill="none" stroke="#8dbf3f" stroke-width="1.5"/></svg>Accommodation</li>
        <li><svg width="8" height="8" viewBox="0 0 8 8"><path d="M1 4l2 2 4-5" fill="none" stroke="#8dbf3f" stroke-width="1.5"/></svg>Meals (breakfast, lunch and dinner)</li>
        <li><svg width="8" height="8" viewBox="0 0 8 8"><path d="M1 4l2 2 4-5" fill="none" stroke="#8dbf3f" stroke-width="1.5"/></svg>Transportation</li>
        <li><svg width="8" height="8" viewBox="0 0 8 8"><path d="M1 4l2 2 4-5" fill="none" stroke="#8dbf3f" stroke-width="1.5"/></svg>Excursions and concerts</li>
        <li><svg width="8" height="8" viewBox="0 0 8 8"><path d="M1 4l2 2 4-5" fill="none" stroke="#8dbf3f" stroke-width="1.5"/></svg>Entry tickets and travel expenses</li>
      </ul>
    </aside>
  </section>

  <section class="itinerary">
    <div class="itinerary-text">
      <h2>SAMPLE ITINERARY</h2>
      <p>A typical ten-day tour begins in Sydney with a harbour walk and school visit, then heads to the Blue Mountains and a wildlife sanctuary before finishing with a farewell concert. Each day balances learning, sightseeing and free time with the group.</p>
      <span class="btn">Learn More</span>
    </div>
    <div class="video">
      <div class="video-frame" role="img" aria-label="Video still of a koala at a wildlife sanctuary"></div>
      <svg class="video-play" width="34" height="24" viewBox="0 0 34 24"><rect width="34" height="24" rx="4" fill="rgba(0,0,0,.6)"/><path d="M14 7l8 5-8 5z" fill="#fff"/></svg>
      <div class="video-bar">
        <svg width="7" height="8" viewBox="0 0 7 8"><path d="M0 0l7 4-7 4z" fill="#fff"/></svg>
        <div class="video-track"></div>
        <svg width="9" height="8" viewBox="0 0 9 8"><path d="M0 3h2l3-3v8L2 5H0z" fill="#fff"/></svg>
      </div>
    </div>
  </section>

  <footer class="site-footer">
    <div class="footer-col">
      <h4>NEWSLETTERS SIGN UP</h4>
      <p>Sign up for tour dates, travel tips and parent news from our team.</p>
      <div class="signup-field">Email address</div>
      <span class="signup-btn">SUBSCRIBE</span>
    </div>
    <div class="footer-col">
      <h4>LATEST TWEET</h4>
      <p>Farewell concert tonight — well done to every student on stage!<br>2 hours ago</p>
    </div>
    <div class="footer-col">
      <h4>GET IN TOUCH</h4>
      <p>Address: 12 Wattle Lane, Surry Hills NSW 2010<br>Phone: +61 2 9000 1234<br>Email: hello@brightwattlejourneys.com.au</p>
    </div>
    <div class="footer-col">
      <h4>FOLLOW US ON</h4>
      <ul class="social">
        <li><span></span>Community</li>
        <li><span></span>Updates</li>
        <li><span></span>Photos</li>
      </ul>
    </div>
  </footer>
  <div class="bottom-bar">Copyright © 2015. All Rights Reserved.</div>
</div>
</body>
</html>
```